Heavy Duty Repairs Poster

Good afternoon - I'm looking for a poster , design to set up around different areas. The Poster must consist of the following
- Heavy duty repairs
- Pictures of Semi trucks , heavy construction equipment , trailers
- Agriculture
- All north American equipment ( see attached pictures)
- Brief Descriptions in bullet point forms
CVIPS
WELDING
AIR CONDITIONING
ENGINE REBUILDS
DIAGONSTICS
FLEET MANAGMENT
TIRE REPAIR AND SALES
ELECTRICAL , HYDRALIC , POWER TRAIN SERVICE AND REPAIRS
PART SALES
FLEET MAINTINACE
DELTEING AND TUNING
AFTER MARKET INSTALLS OUTFITTING
ONSITE & OFFSITE REPAIRS
FULL RECERTIFACTION OVERHAULING
Warranty Approved

Target Market(s)

Heavy Duty Truck , Equipment , Agriculture Owners

Industry/Entity Type

Heavy Duty Repairs

Colors
EB3D1F
EC4F4E
F09395
F8D3D4
FCEDEE

Requirements
Must have
• Pictures of : Semi trucks and trailer , Construction heavy equipment , agriculture equipment
Nice to have
• Flashy and stands out

```html
<!DOCTYPE html>
<html lang="en">
<head>
<meta charset="utf-8">
<title>Heavy Duty Repairs Poster</title>
<link rel="stylesheet" href="https://fonts.googleapis.com/css2?family=Anton&family=Bebas+Neue&family=Archivo+Black&family=Tinos:wght@700&display=swap">
<style>
  :root {
    --red: #eb3d1f;
    --red-band: #e0232b;
    --red-soft: #ec4f4e;
    --pink: #f09395;
    --blush: #f8d3d4;
    --mist: #fcedee;
    --black: #000000;
    --white: #ffffff;
    --silver: #c9c9c9;
  }
  * { margin: 0; padding: 0; box-sizing: border-box; }
  html, body { width: 849px; height: 1200px; overflow: hidden; background: var(--black); }
  .poster {
    position: relative;
    width: 849px;
    height: 1200px;
    overflow: hidden;
    background:
      radial-gradient(ellipse 330px 300px at 444px 520px, rgba(235,61,31,0.85), rgba(160,10,10,0.55) 45%, rgba(60,0,0,0.3) 75%, rgba(0,0,0,0) 100%),
      radial-gradient(ellipse 260px 120px at 560px 800px, rgba(200,20,20,0.45), rgba(0,0,0,0) 100%),
      var(--black);
    font-family: "Bebas Neue", sans-serif;
  }
  .headline-top {
    position: absolute; top: 22px; left: 0; width: 100%;
    text-align: center; color: var(--white);
    font-family: "Anton", sans-serif; font-size: 46px; letter-spacing: 9px; line-height: 1;
  }
  .title-band { position: absolute; top: 78px; left: 0; width: 849px; height: 108px; }
  .title-band svg { position: absolute; inset: 0; }
  .title-all, .title-main, .title-side {
    position: absolute; color: var(--white); font-family: "Anton", sans-serif; line-height: 1;
  }
  .title-all { left: 37px; top: 40px; font-size: 42px; }
  .title-main { left: 107px; top: 20px; font-size: 68px; letter-spacing: -0.5px; }
  .title-side { left: 672px; top: 20px; font-size: 31px; line-height: 34px; }
  .categories {
    position: absolute; top: 203px; left: 0; width: 100%;
    text-align: center; color: var(--white); font-size: 26px; line-height: 1; letter-spacing: 0.3px;
  }
  .categories .sep { color: var(--red-band); margin: 0 3px; }
  .photo-circle {
    position: absolute; top: 270px; width: 146px; height: 146px; border-radius: 50%;
    border: 3px solid var(--red-band);
  }
  .photo-tractor { left: 75px; background: linear-gradient(180deg, #9cb2c4 0%, #6f8a3a 50%, #5a4634 100%); }
  .photo-harvester { left: 267px; background: linear-gradient(180deg, #6d9ed0 0%, #3b7a34 55%, #6d5a42 100%); }
  .photo-trailer { left: 458px; background: radial-gradient(circle at 50% 55%, #d33a2f 0%, #e66b62 30%, #ffffff 60%); }
  .photo-disc { left: 648px; background: linear-gradient(180deg, #9fb7cc 0%, #8aa05a 40%, #3f8a3c 60%, #6a4d36 100%); }
  .photo-semi {
    position: absolute; left: 86px; top: 455px; width: 404px; height: 220px;
    background: linear-gradient(90deg, #c41a1a 0%, #d62828 45%, #e9e9e9 60%, #cfcfcf 100%);
    border-radius: 40px 12px 14px 30px;
  }
  .photo-crane {
    position: absolute; left: 353px; top: 591px; width: 436px; height: 272px;
    background: linear-gradient(160deg, #e8b42a 0%, #d9a11c 50%, #3a3a3a 85%, #1f1f1f 100%);
    border-radius: 14px;
  }
  .services { position: absolute; left: 36px; top: 786px; list-style: none; }
  .services li {
    display: flex; align-items: center; height: 23.2px;
    color: var(--red-band); font-size: 20px; line-height: 1; letter-spacing: 0.1px;
  }
  .services svg { width: 12px; height: 12px; margin-right: 15px; flex: none; }
  .phone {
    position: absolute; left: 478px; top: 980px;
    font-family: "Archivo Black", sans-serif; font-size: 41px; line-height: 1;
    color: var(--red-band); letter-spacing: 0.5px;
  }
  .company {
    position: absolute; left: 440px; top: 1080px; width: 370px; text-align: center;
    font-family: "Tinos", serif; font-weight: 700; color: var(--white); font-size: 26px; line-height: 1;
  }
  .location {
    position: absolute; left: 440px; top: 1116px; width: 370px; text-align: center;
    font-family: "Tinos", serif; font-weight: 700; color: var(--mist); font-size: 20px; line-height: 1;
  }
  .footer-bar { position: absolute; left: 0; bottom: 0; width: 849px; height: 27px; background: var(--red-band); }
</style>
</head>
<body>
<main class="poster">
  <h2 class="headline-top">FIX &amp; REPAIR</h2>

  <header class="title-band">
    <svg width="849" height="108" viewBox="0 0 849 108" aria-hidden="true">
      <polygon fill="var(--silver)" points="0,4 40,0 90,5 160,1 250,6 340,2 430,5 520,1 610,6 700,2 790,5 849,2 849,106 790,101 700,107 610,102 520,106 430,101 340,107 250,102 160,106 90,101 40,107 0,102"/>
      <polygon fill="var(--red-band)" points="0,8 45,4 95,9 165,5 255,10 345,6 435,9 525,5 615,10 705,6 795,9 849,6 849,98 795,94 705,99 615,95 525,99 435,94 345,99 255,95 165,99 95,94 45,99 0,95"/>
    </svg>
    <span class="title-all">ALL</span>
    <h1 class="title-main">HEAVY EQUIPMENT</h1>
    <span class="title-side">INDUSTRYS<br>MACHINES</span>
  </header>

  <p class="categories">SEMI TRUCKS<span class="sep">|</span>HEAVY CONSTRUCTION EQUIPMENT<span class="sep">|</span>TRAILERS<span class="sep">|</span>AGRICULTURE EQUIPMENTS</p>

  <div class="photo-circle photo-tractor" role="img" aria-label="Photo of a large farm tractor in a field"></div>
  <div class="photo-circle photo-harvester" role="img" aria-label="Photo of a green tractor pulling a harvester"></div>
  <div class="photo-circle photo-trailer" role="img" aria-label="Photo of a red farm dump trailer"></div>
  <div class="photo-circle photo-disc" role="img" aria-label="Photo of a green disc harrow on a field"></div>

  <div class="photo-semi" role="img" aria-label="Photo of a red semi truck pulling a white reefer trailer"></div>
  <div class="photo-crane" role="img" aria-label="Photo of a yellow mobile crane truck"></div>

  <ul class="services">
    <li><svg viewBox="0 0 12 12" aria-hidden="true"><rect x="0.5" y="0.5" width="11" height="11" fill="none" stroke="#fff" stroke-width="1"/><path d="M2.5 6 L5 8.5 L10 2.5" fill="none" stroke="#fff" stroke-width="1.4"/></svg>CVIPS</li>
    <li><svg viewBox="0 0 12 12" aria-hidden="true"><rect x="0.5" y="0.5" width="11" height="11" fill="none" stroke="#fff" stroke-width="1"/><path d="M2.5 6 L5 8.5 L10 2.5" fill="none" stroke="#fff" stroke-width="1.4"/></svg>WELDING</li>
    <li><svg viewBox="0 0 12 12" aria-hidden="true"><rect x="0.5" y="0.5" width="11" height="11" fill="none" stroke="#fff" stroke-width="1"/><path d="M2.5 6 L5 8.5 L10 2.5" fill="none" stroke="#fff" stroke-width="1.4"/></svg>AIR CONDITIONING</li>
    <li><svg viewBox="0 0 12 12" aria-hidden="true"><rect x="0.5" y="0.5" width="11" height="11" fill="none" stroke="#fff" stroke-width="1"/><path d="M2.5 6 L5 8.5 L10 2.5" fill="none" stroke="#fff" stroke-width="1.4"/></svg>ENGINE REBUILDS</li>
    <li><svg viewBox="0 0 12 12" aria-hidden="true"><rect x="0.5" y="0.5" width="11" height="11" fill="none" stroke="#fff" stroke-width="1"/><path d="M2.5 6 L5 8.5 L10 2.5" fill="none" stroke="#fff" stroke-width="1.4"/></svg>DIAGONSTICS</li>
    <li><svg viewBox="0 0 12 12" aria-hidden="true"><rect x="0.5" y="0.5" width="11" height="11" fill="none" stroke="#fff" stroke-width="1"/><path d="M2.5 6 L5 8.5 L10 2.5" fill="none" stroke="#fff" stroke-width="1.4"/></svg>FLEET MANAGMENT</li>
    <li><svg viewBox="0 0 12 12" aria-hidden="true"><rect x="0.5" y="0.5" width="11" height="11" fill="none" stroke="#fff" stroke-width="1"/><path d="M2.5 6 L5 8.5 L10 2.5" fill="none" stroke="#fff" stroke-width="1.4"/></svg>TIRE REPAIR AND SALES</li>
    <li><svg viewBox="0 0 12 12" aria-hidden="true"><rect x="0.5" y="0.5" width="11" height="11" fill="none" stroke="#fff" stroke-width="1"/><path d="M2.5 6 L5 8.5 L10 2.5" fill="none" stroke="#fff" stroke-width="1.4"/></svg>ELECTRICAL, HYDRALIC, POWER TRAIN SERVICE AND REPAIRS</li>
    <li><svg viewBox="0 0 12 12" aria-hidden="true"><rect x="0.5" y="0.5" width="11" height="11" fill="none" stroke="#fff" stroke-width="1"/><path d="M2.5 6 L5 8.5 L10 2.5" fill="none" stroke="#fff" stroke-width="1.4"/></svg>PART SALES</li>
    <li><svg viewBox="0 0 12 12" aria-hidden="true"><rect x="0.5" y="0.5" width="11" height="11" fill="none" stroke="#fff" stroke-width="1"/><path d="M2.5 6 L5 8.5 L10 2.5" fill="none" stroke="#fff" stroke-width="1.4"/></svg>FLEET MAINTINACE</li>
    <li><svg viewBox="0 0 12 12" aria-hidden="true"><rect x="0.5" y="0.5" width="11" height="11" fill="none" stroke="#fff" stroke-width="1"/><path d="M2.5 6 L5 8.5 L10 2.5" fill="none" stroke="#fff" stroke-width="1.4"/></svg>DELTEING AND TUNING</li>
    <li><svg viewBox="0 0 12 12" aria-hidden="true"><rect x="0.5" y="0.5" width="11" height="11" fill="none" stroke="#fff" stroke-width="1"/><path d="M2.5 6 L5 8.5 L10 2.5" fill="none" stroke="#fff" stroke-width="1.4"/></svg>AFTER MARKET INSTALLS OUTFITTING</li>
    <li><svg viewBox="0 0 12 12" aria-hidden="true"><rect x="0.5" y="0.5" width="11" height="11" fill="none" stroke="#fff" stroke-width="1"/><path d="M2.5 6 L5 8.5 L10 2.5" fill="none" stroke="#fff" stroke-width="1.4"/></svg>ONSITE &amp; OFFSITE REPAIRS</li>
    <li><svg viewBox="0 0 12 12" aria-hidden="true"><rect x="0.5" y="0.5" width="11" height="11" fill="none" stroke="#fff" stroke-width="1"/><path d="M2.5 6 L5 8.5 L10 2.5" fill="none" stroke="#fff" stroke-width="1.4"/></svg>FULL RECERTIFACTION OVERHAULING</li>
    <li><svg viewBox="0 0 12 12" aria-hidden="true"><rect x="0.5" y="0.5" width="11" height="11" fill="none" stroke="#fff" stroke-width="1"/><path d="M2.5 6 L5 8.5 L10 2.5" fill="none" stroke="#fff" stroke-width="1.4"/></svg>WARRANTY APPROVED</li>
  </ul>

  <p class="phone">780-555-0147</p>
  <p class="company">Ridgeline Heavy Repair</p>
  <p class="location">Elmsford , Alberta</p>

  <div class="footer-bar"></div>
</main>
</body>
</html>
```